Varnik Holdings — Business Card Design Brief
Overview
Design a double-sided business card for Varnik Holdings that highlights our two service arms: Varnik Communications (telecommunications) and Varnik Energy (business energy solutions). The card should feel smart and stand out when handed to clients.

Objectives
Showcase our areas of specialty clearly.
Reflect the overall Varnik / Varnik Holdings brand while acknowledging both arms.
Explore using both logos (Communications + Energy) or one unified logo, depending on the design.

Deliverables
One double-sided business card design (front + back).

Content & Copy
Front (preferred): Logo: Varnik / Varnik Holdings
Descriptor: Business Communications | Business Energy
Back:My contact details and company details
Core products: Business Mobile • Telephony • Internet • Business Energy Solutions

Brand & Visual Direction
We have a group logo currently tailored more toward telecoms, plus a separate Varnik Energy logo.
Please explore layouts that use both logos or just one, whichever works best.
Color: I wouldn't mind seeing an option using our the Blue/Purple gradient from our website (varnik-example.co.uk), but also open to non-gradient approaches and other colours..

Overall look: Smart, modern, and distinctive.
Format & Print Specs
Double-sided business card format. (Use a standard size

Must-Haves
Front: Varnik wording or Varnik Holdings wording with atleast 1 logo also on front “Business Communications | Business Energy.”

Back: Contact + company details and core products.
A design that stands out while remaining professional.

Nice-to-Have Options
A gradient version using our site’s Blue/Purple gradient.
A non-gradient version.
A dual-logo treatment versus a single-logo treatment.

Thanks
Owen

```html
<!DOCTYPE html>
<html lang="en">
<head>
<meta charset="utf-8">
<title>Varnik Holdings – Business Card</title>
<link href="https://fonts.googleapis.com/css2?family=Lato:wght@400;700;900&display=swap" rel="stylesheet">
<style>
  :root {
    --bg: #2c2e30;
    --purple: #8a0dc6;
    --navy: #1c1560;
    --deep-blue: #1a4a94;
    --blue: #1a6fd6;
    --sky: #12a7df;
    --green: #3aa61f;
    --ink: #222;
    --muted: #4a4a5a;
    --white: #ffffff;
  }
  * { box-sizing: border-box; margin: 0; padding: 0; }
  html, body { width: 1200px; height: 1122px; overflow: hidden; }
  body {
    background: var(--bg);
    font-family: "Lato", sans-serif;
    display: flex; flex-direction: column; align-items: center; justify-content: center;
    gap: 44px;
  }
  .card {
    width: 880px; height: 500px; border-radius: 28px;
    position: relative; overflow: hidden;
  }

  /* Front */
  .card-front {
    background: linear-gradient(90deg, var(--purple) 0%, var(--navy) 30%, var(--navy) 70%, var(--deep-blue) 100%);
    color: var(--white);
  }
  .brand-divider {
    position: absolute; left: 440px; top: 110px; width: 2px; height: 170px;
    background: linear-gradient(180deg, transparent, var(--purple), transparent);
  }
  .brand {
    position: absolute; top: 150px; display: flex; align-items: center; gap: 18px;
  }
  .brand-comms { left: 110px; }
  .brand-energy { left: 510px; }
  .brand-dot { width: 58px; height: 58px; border-radius: 50%; flex: none; }
  .brand-comms .brand-dot { background: var(--blue); }
  .brand-energy .brand-dot { background: var(--green); }
  .brand-name { font-weight: 900; font-size: 64px; letter-spacing: 1px; text-transform: uppercase; }
  .descriptor {
    position: absolute; left: 0; right: 0; top: 300px; text-align: center;
    font-size: 20px; font-weight: 700; letter-spacing: 3px; text-transform: uppercase;
  }
  .descriptor .bar { color: var(--purple); margin: 0 14px; }
  .products {
    position: absolute; left: 0; right: 0; bottom: 70px; text-align: center;
    font-size: 17px; letter-spacing: 1px; text-transform: uppercase;
  }
  .products .sep { color: var(--purple); margin: 0 8px; }

  /* Back */
  .card-back { background: var(--white); }
  .back-brand {
    position: absolute; left: 60px; top: 60px; display: flex; align-items: center; gap: 16px;
  }
  .back-brand .brand-dot { background: var(--sky); width: 70px; height: 70px; }
  .back-brand .brand-name { color: var(--blue); font-size: 58px; }
  .energy-tag {
    position: absolute; left: 60px; bottom: 38px;
    font-weight: 900; font-size: 22px; color: var(--green); text-transform: uppercase;
  }
  .person { position: absolute; left: 60px; top: 250px; }
  .person-name { font-weight: 900; font-size: 46px; color: var(--navy); letter-spacing: 1px; }
  .person-role { font-size: 26px; color: var(--purple); margin-top: 4px; }
  .person-rule { width: 180px; height: 2px; background: var(--blue); margin-top: 18px; }

  .contact { position: absolute; left: 500px; top: 190px; font-size: 21px; color: var(--ink); }
  .contact-row { display: flex; gap: 14px; align-items: flex-start; margin-bottom: 10px; }
  .contact-row svg { width: 20px; height: 20px; margin-top: 4px; flex: none; fill: var(--purple); }
  .contact-lines p { line-height: 1.35; }
  .company { font-weight: 700; }
  .company .c-navy { color: var(--navy); }
  .company .c-blue { color: var(--blue); }
  .company .c-green { color: var(--green); }

  .back-products {
    position: absolute; right: 50px; bottom: 42px;
    font-size: 13px; font-weight: 700; letter-spacing: 0.5px; text-transform: uppercase;
    color: var(--muted);
  }
  .back-products .sep { color: var(--purple); margin: 0 6px; }
</style>
</head>
<body>

<section class="card card-front">
  <div class="brand brand-comms">
    <span class="brand-dot"></span>
    <span class="brand-name">Varnik</span>
  </div>
  <div class="brand-divider"></div>
  <div class="brand brand-energy">
    <span class="brand-dot"></span>
    <span class="brand-name">Varnik</span>
  </div>
  <p class="descriptor">Business Communications<span class="bar">|</span>Business Energy</p>
  <p class="products">Business Mobile<span class="sep">•</span>Telephony<span class="sep">•</span>Internet<span class="sep">•</span>Business Energy Solutions</p>
</section>

<section class="card card-back">
  <div class="back-brand">
    <span class="brand-dot"></span>
    <span class="brand-name">Varnik</span>
  </div>

  <div class="person">
    <h1 class="person-name">DANIEL HART</h1>
    <p class="person-role">Managing Director &amp; CEO</p>
    <div class="person-rule"></div>
  </div>

  <div class="contact">
    <div class="contact-row">
      <svg viewBox="0 0 24 24" aria-hidden="true"><path d="M12 2a7 7 0 0 0-7 7c0 5 7 13 7 13s7-8 7-13a7 7 0 0 0-7-7zm0 9.5A2.5 2.5 0 1 1 12 6.5a2.5 2.5 0 0 1 0 5z"/></svg>
      <div class="contact-lines">
        <p class="company"><span class="c-navy">Varnik</span> <span class="c-blue">Communications</span> <span class="c-navy">+</span> <span class="c-green">Energy</span></p>
        <p>24 Harlow Lane, Manchester</p>
        <p>England, M1 0XX</p>
      </div>
    </div>
    <div class="contact-row">
      <svg viewBox="0 0 24 24" aria-hidden="true"><path d="M6.6 10.8a15 15 0 0 0 6.6 6.6l2.2-2.2a1 1 0 0 1 1-.25 11.4 11.4 0 0 0 3.6.57 1 1 0 0 1 1 1V20a1 1 0 0 1-1 1A17 17 0 0 1 3 4a1 1 0 0 1 1-1h3.5a1 1 0 0 1 1 1c0 1.25.2 2.45.57 3.6a1 1 0 0 1-.25 1z"/></svg>
      <p>+44 0161 000 0123</p>
    </div>
    <div class="contact-row">
      <svg viewBox="0 0 24 24" aria-hidden="true"><path d="M2 5h20v14H2zm2 2v.5l8 5 8-5V7l-8 5z"/></svg>
      <p>info@varnik-example.co.uk</p>
    </div>
    <div class="contact-row">
      <svg viewBox="0 0 24 24" aria-hidden="true"><path d="M12 2a10 10 0 1 0 0 20 10 10 0 0 0 0-20zm6.9 9h-3a15 15 0 0 0-1.4-6 8 8 0 0 1 4.4 6zM12 4c1 1.3 1.8 3.9 2 7h-4c.2-3.1 1-5.7 2-7zM9.5 5a15 15 0 0 0-1.4 6h-3a8 8 0 0 1 4.4-6zM5.1 13h3a15 15 0 0 0 1.4 6 8 8 0 0 1-4.4-6zM12 20c-1-1.3-1.8-3.9-2-7h4c-.2 3.1-1 5.7-2 7zm2.5-1a15 15 0 0 0 1.4-6h3a8 8 0 0 1-4.4 6z"/></svg>
      <p>varnik-example.co.uk</p>
    </div>
  </div>

  <p class="energy-tag">Varnik Energy</p>
  <p class="back-products">Business Mobile<span class="sep">•</span>Telephony<span class="sep">•</span>Internet<span class="sep">•</span>Business Energy Solutions</p>
</section>

</body>
</html>
```